Business Card Design

Business Card for professional consulting firm working with large financial institutions.

Target Market(s)

Executive buyers

Industry/Entity Type

Banking

Contact Information for Business Card

Mild creativity wanted. Not boring, but do elaborate artwork.

Font styles to use
Serif
Sans Serif

Colors

Designer to choose colors to be used in the design.

Requirements
Must have
• Standard business card features - company name, individual name, telephone, website, email, locations.
Nice to have
• Two colors
Should not have
• too many colors, fancy printing, cartoons.

```html
<!DOCTYPE html>
<html lang="en">
<head>
<meta charset="UTF-8">
<title>Veralund Business Card</title>
<link href="https://fonts.googleapis.com/css2?family=Fira+Sans:wght@400;600&family=Noto+Serif:wght@400&display=swap" rel="stylesheet">
<style>
  :root {
    --backdrop: #3b3b3c;
    --card: #1e1e1f;
    --ink: #f2f2f2;
    --ink-soft: #c9c9c9;
    --emboss: #2c2c2d;
    --rule: #bdbdbd;
  }
  * { box-sizing: border-box; margin: 0; padding: 0; }
  html, body { width: 799px; height: 1200px; overflow: hidden; }
  body {
    background: var(--backdrop);
    position: relative;
    font-family: "Noto Serif", serif;
  }
  .card {
    position: absolute;
    left: 90px;
    width: 620px;
    height: 354px;
    background: var(--card);
    border-radius: 3px;
  }
  .card--front { top: 170px; }
  .card--back { top: 676px; }

  .front-brand {
    position: absolute;
    left: 0; right: 0; top: 150px;
    text-align: center;
    font-family: "Noto Serif", serif;
    font-size: 46px;
    color: var(--emboss);
    letter-spacing: 1px;
  }

  .holder-name {
    position: absolute;
    left: 40px; top: 58px;
    font-family: "Fira Sans", sans-serif;
    font-weight: 600;
    font-size: 24px;
    color: var(--ink);
  }
  .holder-role {
    position: absolute;
    left: 40px; top: 92px;
    font-family: "Fira Sans", sans-serif;
    font-size: 14px;
    color: var(--ink-soft);
  }
  .divider {
    position: absolute;
    left: 200px; top: 112px;
    width: 370px; height: 1px;
    background: var(--rule);
  }
  .contact-list {
    position: absolute;
    left: 40px; top: 138px;
    list-style: none;
  }
  .contact-list li {
    display: flex;
    align-items: center;
    gap: 12px;
    height: 25px;
    font-size: 14px;
    color: var(--ink);
  }
  .contact-list svg { width: 14px; height: 14px; fill: none; stroke: var(--ink); stroke-width: 1.6; }
  .back-brand {
    position: absolute;
    right: 50px; top: 40px;
    font-family: "Noto Serif", serif;
    font-size: 36px;
    color: var(--ink);
    letter-spacing: 0.5px;
  }
  .address {
    position: absolute;
    left: 330px; top: 262px;
    font-size: 15px;
    line-height: 26px;
    color: var(--ink);
    font-style: normal;
  }
</style>
</head>
<body>
  <section class="card card--front">
    <div class="front-brand">veralund</div>
  </section>

  <section class="card card--back">
    <h1 class="holder-name">John Doe Smith</h1>
    <p class="holder-role">Managing Director</p>
    <div class="divider"></div>
    <ul class="contact-list">
      <li>
        <svg viewBox="0 0 16 16"><path d="M3 2h3l1 4-2 1a8 8 0 0 0 4 4l1-2 4 1v3a1 1 0 0 1-1 1C7 14 2 9 2 3a1 1 0 0 1 1-1z"/></svg>
        555.555.5555
      </li>
      <li>
        <svg viewBox="0 0 16 16"><rect x="1.5" y="3.5" width="13" height="9"/><path d="M1.5 3.5 8 9l6.5-5.5"/></svg>
        johndoe@example.com
      </li>
      <li>
        <svg viewBox="0 0 16 16"><circle cx="8" cy="8" r="6.5"/><path d="M1.5 8h13M8 1.5c-3 3.5-3 9.5 0 13M8 1.5c3 3.5 3 9.5 0 13"/></svg>
        www.yourwebsite.com
      </li>
    </ul>
    <div class="back-brand">veralund</div>
    <address class="address">234 Anywhere St., Any City,<br>Any Town, US 123456</address>
  </section>
</body>
</html>
```